Verdant Systems Business Card

want the back of card to be blue- with the logo in the center
front of card- info plus logo (info being mailing address, email address, and website address )
4 different names with titles to have on cards
1) Calvin Borsted - Owner
2) Naomi Trelvik- Customer Relationship Specialist
3) Felix Andrade- Vice President of Sales
4) Owen Markby- Chief Technology Officer

Target Market(s)

tech company in the government/probation office industry

Industry/Entity Type

Government Office

Contact Information for Business Card

1) Calvin Borsted - Owner

Colors
0355a3
ffffff

Requirements
Must have
• back side should be blue, with the logo placed in the center
• front side needs to include both the logo, as well as company info (info should include website address, email address, and mailing address)

```html
<!DOCTYPE html>
<html lang="en">
<head>
<meta charset="utf-8">
<title>Verdant Systems Business Card</title>
<link href="https://fonts.googleapis.com/css2?family=Cinzel:wght@600&family=Open+Sans:wght@400;700&display=swap" rel="stylesheet">
<style>
  :root {
    --brand-blue: #0355a3;
    --card-blue: #0b55a6;
    --band-grey: #86878b;
    --text-grey: #6d6e72;
    --white: #ffffff;
    --stage: #ecebe8;
  }
  * { margin: 0; padding: 0; box-sizing: border-box; }
  html, body { width: 900px; height: 1200px; overflow: hidden; }
  body { background: var(--stage); position: relative; font-family: "Open Sans", sans-serif; }

  .card {
    position: absolute;
    border-radius: 22px;
    overflow: hidden;
    box-shadow: 0 4px 10px rgba(0,0,0,0.25);
  }

  /* Front side */
  .card-front { left: 87px; top: 137px; width: 733px; height: 428px; background: var(--white); }
  .front-brand {
    position: absolute; right: 52px; top: 140px;
    display: flex; align-items: center; gap: 10px; white-space: nowrap;
    font-family: "Cinzel", serif; font-weight: 600; color: var(--brand-blue);
    font-size: 25px; line-height: 1; letter-spacing: 0.5px;
  }
  .brand-square { width: 13px; height: 13px; background: var(--brand-blue); flex: none; }
  .holder-name {
    position: absolute; left: 53px; top: 212px;
    font-family: "Cinzel", serif; font-weight: 600; color: var(--brand-blue);
    font-size: 28px; letter-spacing: 0.5px; white-space: nowrap;
  }
  .holder-title { position: absolute; left: 53px; top: 252px; font-size: 16px; color: var(--text-grey); }
  .contact-list { position: absolute; left: 52px; top: 290px; list-style: none; }
  .contact-list li {
    display: flex; align-items: center; gap: 9px; white-space: nowrap;
    height: 27px; font-size: 15.5px; color: var(--text-grey);
  }
  .contact-list svg { width: 13px; height: 13px; fill: var(--brand-blue); flex: none; }
  .band { position: absolute; bottom: 0; height: 14px; }
  .band-blue { left: 0; width: 423px; background: var(--brand-blue); }
  .band-grey { left: 430px; right: 0; background: var(--band-grey); }

  /* Back side */
  .card-back { left: 87px; top: 632px; width: 735px; height: 431px; background: var(--card-blue); }
  .back-brand {
    position: absolute; left: 0; right: 0; top: 200px;
    display: flex; justify-content: center; align-items: center; gap: 16px; white-space: nowrap;
    font-family: "Cinzel", serif; font-weight: 600; color: var(--white);
    font-size: 52px; line-height: 1; letter-spacing: 1px;
  }
  .back-brand .brand-square { width: 22px; height: 22px; background: var(--white); }
  .back-web {
    position: absolute; left: 0; right: 0; top: 379px; text-align: center;
    font-weight: 700; font-size: 16.5px; color: var(--white); letter-spacing: 0.3px;
  }
</style>
</head>
<body>
  <section class="card card-front">
    <div class="front-brand"><span class="brand-square"></span><span>Verdant Systems</span></div>
    <h1 class="holder-name">CALVIN BORSTED</h1>
    <p class="holder-title">Owner</p>
    <ul class="contact-list">
      <li>
        <svg viewBox="0 0 16 16" aria-hidden="true"><path d="M3.6 1l2.3 3.2-1.4 1.6c.9 2 2.6 3.7 4.7 4.7l1.6-1.4L14 11.4 12.6 14C6.5 13.6 2.4 9.5 2 3.4z"/></svg>
        <span>000 000 0000</span>
      </li>
      <li>
        <svg viewBox="0 0 16 16" aria-hidden="true"><path d="M1 3h14v1.2L8 9 1 4.2z"/><path d="M1 5.8l7 4.8 7-4.8V13H1z"/></svg>
        <span>calvin@verdantsystems.com</span>
      </li>
      <li>
        <svg viewBox="0 0 16 16" aria-hidden="true"><path d="M8 1a7 7 0 100 14A7 7 0 008 1zm0 1.3c.9 0 1.8 1.7 2.1 4.1H5.9C6.2 4 7.1 2.3 8 2.3zM2.4 6.4a5.7 5.7 0 012.7-3.4c-.5 1-.8 2.1-.9 3.4zm0 1.3h1.8c.1 1.3.4 2.4.9 3.4a5.7 5.7 0 01-2.7-3.4zm3.5 0h4.2c-.3 2.4-1.2 4-2.1 4s-1.8-1.6-2.1-4zm5.9 0h1.8a5.7 5.7 0 01-2.7 3.4c.5-1 .8-2.1.9-3.4zm0-1.3c-.1-1.3-.4-2.4-.9-3.4a5.7 5.7 0 012.7 3.4z"/></svg>
        <span>www.verdantsystems.com</span>
      </li>
      <li>
        <svg viewBox="0 0 16 16" aria-hidden="true"><path d="M8 1a5 5 0 00-5 5c0 3.8 5 9 5 9s5-5.2 5-9a5 5 0 00-5-5zm0 6.8A1.8 1.8 0 118 4.2a1.8 1.8 0 010 3.6z"/></svg>
        <span>1200 Meridian Ave, Suite 4, Lakeport, OH 40000</span>
      </li>
    </ul>
    <div class="band band-blue"></div>
    <div class="band band-grey"></div>
  </section>

  <section class="card card-back">
    <div class="back-brand"><span class="brand-square"></span><span>Verdant Systems</span></div>
    <p class="back-web">www.verdantsystems.com</p>
  </section>
</body>
</html>
```